Vetern Mailer for Mortgage Refinance

Hello, I need some options in my KB mailers we send out here in the USA! A sample of our mailer has been included. I need all the verbiage the same. The data merge points need to stay on too. Please make this pop. We have a high end PELDO printer and a Z auto folding machine. Letter goes into a number 10 envelope with windows. So lets see what you can do. One with colors below is our company colors and then one black, white, gray.
Blue - 3399FF------ R 51 G 153 B 255
Orange - FF9933----- R 255 G 153 B 51
Black – 333333------ R 51 G 51 B 51
White – FFFFFF------ R 255 G 255 B 255

Target Market(s)

United States Military Service Members

Industry/Entity Type

Mortgage Lender

Requirements
Must have
• Margins for folding with Z and Number 10 Envelope with two windows

```html
<!DOCTYPE html>
<html lang="en">
<head>
<meta charset="utf-8">
<title>KB Refinance Mailer – Front and Back</title>
<link rel="stylesheet" href="https://fonts.googleapis.com/css2?family=Montserrat:wght@300;400;500;600;700;800&display=swap">
<style>
:root{
  --blue:#3399ff;
  --orange:#ff9933;
  --ink:#333333;
  --white:#ffffff;
  --panel:#e6e6e6;
  --stage:#707070;
}
*{box-sizing:border-box;margin:0;padding:0}
html,body{width:752px;height:1200px;overflow:hidden;background:var(--stage)}
body{font-family:"Montserrat",Arial,sans-serif;color:var(--ink);position:relative}
.sheet{position:absolute;left:150px;width:752px;height:973px;background:var(--white);overflow:hidden;transform:scale(.6);transform-origin:0 0}
.sheet.front{top:10px}
.sheet.back{top:606px}
.abs{position:absolute}
.re{left:69px;top:30px;font-size:13px;line-height:19px}
.notice{left:47px;top:112px;font-size:10px;line-height:13px}
.recipient{left:69px;top:160px;font-size:13px;line-height:20px}
.brand{font-size:25px;font-weight:300;letter-spacing:3px;color:var(--blue);line-height:30px;text-align:right}
.brand small{display:block;font-size:14px;letter-spacing:5px}
.front .brand{left:452px;top:58px;width:256px}
.greeting{left:53px;top:283px;font-size:15px;font-weight:600;color:var(--blue)}
.body-copy{left:53px;top:318px;width:350px;font-size:13.4px;line-height:21px}
.body-copy .hl{color:var(--blue);font-weight:600}
.callout{left:53px;top:568px;width:320px;font-size:15.5px;line-height:20px;font-weight:700;color:var(--orange)}
.body-copy.second{top:626px}
sup{font-size:7px}
.loan-id{left:53px;top:762px;font-size:17px;font-weight:600;color:var(--orange)}
.call{left:53px;top:795px;font-size:15px;line-height:20px}
.call .phone{display:block;font-size:22px;font-weight:700;color:var(--blue);line-height:28px}
.company{font-size:10px;line-height:16px}
.company b{font-weight:800}
.front .company{left:53px;top:897px}
.rule{position:absolute;bottom:8px;height:4px}
.rule.blue{left:0;width:415px;background:var(--blue)}
.rule.orange{left:438px;right:0;background:var(--orange)}
.side{left:440px;top:197px;width:268px;display:flex;flex-direction:column}
.skip-box{background:var(--blue);color:var(--white);border-radius:6px 6px 0 0;text-align:center;padding:10px 0 6px;font-size:15px;line-height:22px;font-weight:600}
.skip-box .amount{font-size:44px;font-weight:800;line-height:54px}
.benefits{background:var(--panel);padding:12px 20px 16px 28px;font-size:12.8px;line-height:20px}
.benefits .lead{text-align:center;font-size:16px;line-height:22px;margin:0 -8px 20px -14px}
.benefits h3{font-size:14.5px;font-weight:700;margin-bottom:3px}
.benefits ul{list-style:none;margin-bottom:26px}
.benefits ul:last-child{margin-bottom:0}
.benefits li{position:relative;padding-left:14px}
.benefits li::before{content:"";position:absolute;left:0;top:8px;width:4px;height:4px;border-radius:50%;background:var(--ink)}
.cashout{background:var(--orange);color:var(--white);border-radius:0 0 6px 6px;text-align:center;padding:12px 0 8px;font-size:16px;line-height:20px}
.cashout .amount{font-size:43px;font-weight:800;line-height:50px}
.reverse-note{left:440px;top:935px;width:268px;text-align:right;font-size:11.5px}
.reverse-note span{color:var(--blue);font-weight:700}
.disclaimer{left:69px;top:74px;width:614px;font-size:7.6px;line-height:11.6px;text-align:justify}
.disclaimer p{margin-bottom:9px}
.back .brand{left:248px;top:760px;width:256px;text-align:center}
.back .call{left:102px;top:876px;font-size:13px;line-height:18px}
.back .call .phone{font-size:17px;line-height:22px}
.back .company{left:424px;top:886px}
</style>
</head>
<body>
<main class="sheet front">
  <p class="abs re">RE: &lt;&lt;lender&gt;&gt;<br>Loan ID Number: &lt;&lt;loan_id&gt;&gt;</p>
  <p class="abs notice">Highpoint Home Loans LLC Is not affiliated with your<br>current lender nor is it an agency of the Federal Government.</p>
  <p class="abs recipient">&lt;&lt;first_name&gt;&gt; &lt;&lt;last_name&gt;&gt;<br>&lt;&lt;address&gt;&gt;<br>&lt;&lt;city_state_zip&gt;&gt;</p>
  <div class="abs brand">HIGHPOINT<small>Home Loans</small></div>

  <p class="abs greeting">Dear &lt;&lt;first_name&gt;&gt;,</p>
  <p class="abs body-copy">We are contacting you regarding your &lt;&lt;balance&gt;&gt; KB loan. Our review has indicated that because of homes appreciating in &lt;&lt;city&gt;&gt;, you may now qualify for additional benefits. These benefits may include lowering your monthly mortgage payment, deferring up to two payments, refund of escrow, and <span class="hl">$35,000</span> or more cash-out.<sup>3</sup> Call our KB Program Specialist at &lt;&lt;phone_number&gt;&gt; at your earliest convenience to receive a detailed explanation of how you may be able to access these benefits.<sup>4</sup></p>
  <p class="abs callout">You may also receive a check back from your escrow account.<sup>2</sup></p>
  <p class="abs body-copy second">We recommend you call our office at &lt;&lt;phone_number&gt;&gt; within the next 3-5 business days as market rates fluctuate. By taking action now your next mortgage payment may not be due until &lt;&lt;next_pay_month&gt;&gt;.2 To avoid further delay, please call today.</p>
  <p class="abs loan-id">Loan ID Number: &lt;&lt;loan_id&gt;&gt;</p>
  <p class="abs call">Call toll-free<span class="phone">&lt;&lt;phone_number&gt;&gt;</span>Weekdays 6 a.m. to 5 p.m. PST</p>
  <p class="abs company"><b>Highpoint Home Loans LLC</b><br>NMLS 4418260 20710 &nbsp;&nbsp;|&nbsp;&nbsp; N Harbor Rd<br>Ste 210 &nbsp;&nbsp;|&nbsp;&nbsp; Mesa &nbsp;&nbsp;|&nbsp;&nbsp; AZ 85201</p>

  <aside class="abs side">
    <div class="skip-box">&lt;&lt;close_month&gt;&gt; &amp;<br>&lt;&lt;skip_month&gt;&gt;<div class="amount">$000</div></div>
    <div class="benefits">
      <p class="lead">You may be able to defer your next two payments.<sup>1</sup></p>
      <h3>Additional Benefits Include:</h3>
      <ul>
        <li>100% LTV Cash-Out Available</li>
        <li>Pay off High Interest Debt</li>
        <li>Complete a long overdue home renovation</li>
        <li>No out-of-pocket appraisal deposit</li>
        <li>No Private Mortgage Insurance</li>
      </ul>
      <h3>KB IRRRL Benefits:</h3>
      <ul>
        <li>Reduce Your Current Interest Rate</li>
        <li>Mortgage-Only Credit Report</li>
        <li>No Appraisal Required</li>
        <li>Fast Closings in 8-14 days</li>
        <li>No Income or Asset Verification Required</li>
      </ul>
    </div>
    <div class="cashout">Cash Out Options (Tax Free):<div class="amount">$35,000</div>or more</div>
  </aside>
  <p class="abs reverse-note">*Please see reverse for disclaimer <span>›››</span></p>

  <div class="rule blue"></div>
  <div class="rule orange"></div>
</main>

<section class="sheet back">
  <div class="abs disclaimer">
    <p>Offer is available only for loans made or arranged through Highpoint Home Loans LLC, NMLS# 4418260, 20710 N. Harbor Road, Ste. 210, Mesa, AZ 85201, who is not associated with, or acting on behalf of your current lender or any government agency. Verification of employment may apply. This program is exclusive to the beneficiary named above and is nontransferable.</p>
    <p>TERMS AND CONDITIONS: This offer is extended because you appear to satisfy certain credit derived from information contained in a pre-screened report received from a credit reporting agency used by us. The amount and terms of any credit offer we extend to you will be determined by your credit history, your capability to make payments and available equity in your home. The minimum loan amount shall be no less than $80,000.00. You may no longer qualify if you do not continue to meet the criteria used to select your name for this offer or any applicable criteria on credit worthiness or if you do not or can't furnish any required collateral. To qualify for this offer you may be required to provide up to two years of income verification. This offer is made under the assumption that your debt-to-income ratio can't exceed 50%; other programs may be available with a higher level of debt. Credit severity may affect down payment. The lender may also choose to cancel this offer if it is unable to verify the information you have provided. All bankruptcies must be discharged. The lender or an affiliated lender must be in a valid first or second lien position and property hazard insurance is required. Additional information and documentation may be needed to issue loan commitment. The amount of the pre-selected new home loan is based on the current balance that is coming from the information received from one of three credit reporting agencies: Northline, Crestview, or Baymark.</p>
    <p>State Disclosure Requirements: Highpoint Home Loans, LLC is a licensed mortgage lender/broker. The following states require disclosure of licensing information. (If your state is not listed, it doesn't require a specific license disclosure):</p>
    <p>AZ Department of Insurance and Financial Institutions License #: 1047326 &amp; 4418260, CA Licensed by the Department of Financial Protection and Innovation (DFPI) under the California Residential Mortgage Lending Act, License #: 60DBO-204417 &amp; 4418260, CO Department of Regulatory Agencies License #: 4418260, FL Office of Financial Regulation License #: MLD3341 &amp; 4418260, ID Mortgage Broker/Lender License #: MBL-2084418260 &amp; 4418260, MT Banking &amp; Financial Institutions License #: 4418260, OR Division of Financial Regulation License #: 4418260, TN Department of Financial Institutions #: 4418260, TX SML Mortgage Company License #: 4418260, Highpoint Home Loans LLC, 20710 N Harbor Road Suite 210, Mesa, AZ 85201, 4418260, Residential Mortgage Loan Company, UT Department of Commerce License #: 13307614 &amp; 4418260, WA Department of Financial Institutions License #: CL-4418260 &amp; 4418260, www.licenselookup-example.org.</p>
    <p>1. Deferred mortgage payments: If you do not make your mortgage payment for the month that you are closing your new loan, it may be possible to capitalize that payment into your new loan, thereby deferring the due date of your next mortgage payment to be due 1-2 months. Please be aware that deferring your mortgage payment as described may result in additional interest charges over the life of your loan. This deferred interest will be added to the principal balance of your new loan, potentially increasing your future monthly payments and the total amount payable over the term of your mortgage. Additionally, it is important to understand the implications of late payments. While your mortgage payment is not considered officially late on your credit until 30-days past the due date, there may be late fees incurred if the payment is not received within 15-days of the due date. Please note that a grace period of 15-days is typically provided; however, payments received after this period may attract a late fee as per the terms of your loan agreement. We encourage you to manage your payments responsibly to avoid any additional charges and to maintain a healthy credit status.</p>
    <p>2. Escrow Account Refund (if applicable): If you have an escrow account associated with your mortgage, please be aware that any refund from this account is governed by the terms and conditions of your current lender. The timing and amount of a potential refund depend on the account balance at the time of loan payoff, along with specific escrow requirements. For those without an escrow account, this clause does not apply. We advise all borrowers to reach out to their current lender for detailed information about their escrow account status and any refund eligibility that may pertain.</p>
    <p>3. Example cash-out of $35,000 will be in addition to your monthly mortgage payment. Cash-out offer assumes you have adequate equity in your property. A full appraisal will be required with your loan application to determine the actual value. Your actual rate and payment may be different based on many factors. Please contact one of our Licensed Lending Officers at 855-410-2276 for a customized rate and payment quote. Cash-out offers may not be available in TX.</p>
    <p>4. Your circumstances may vary, so please contact 855-410-2276 to see how we may assist.</p>
    <p>Highpoint Home Loans is an Equal Housing Lender. As prohibited by federal law, we do not engage in business practices that discriminate on the basis of race, color, religion, national origin, sex, marital status, age (provided you have the capacity to enter into a binding contract), because all or part of your income may be derived from any public assistance program, or because you have, in good faith, exercised any right under the Consumer Credit Protection Act. The federal agency that administers our compliance with these federal laws is the Federal Trade Commission, Equal Credit Opportunity, Washington, DC, 20580.</p>
  </div>

  <div class="abs brand">HIGHPOINT<small>Home Loans</small></div>
  <p class="abs call">Call toll-free<span class="phone">&lt;&lt;phone_number&gt;&gt;</span>Weekdays 6 a.m. to 5 p.m. PST</p>
  <p class="abs company"><b>Highpoint Home Loans LLC</b><br>NMLS 4418260 20710 &nbsp;&nbsp;|&nbsp;&nbsp; N Harbor Rd<br>Ste 210 &nbsp;&nbsp;|&nbsp;&nbsp; Mesa &nbsp;&nbsp;|&nbsp;&nbsp; AZ 85201</p>

  <div class="rule blue"></div>
  <div class="rule orange"></div>
</section>
</body>
</html>
```